Government Contracting business needs a website design.

Pellworth & Quine, LLC is a minority owned Service Disabled Veteran Owned Small Business (SDVOSB) that provides Strategic Planning, Public Health Emergency Response, and Data Management Solutions for Federal Civilian and Defense Agencies. We have over 20 years of experience helping health and defense agencies develop concept of operations, deploy assets and personnel in Hot Zones around the world, and deliver goods and services all of the globe.

We are a leader in the field of Data Management. We help our customers develop cloud migration and disaster recovery strategies. We are experts with database management, data replication, queries, consolidation, and records management.

We are looking for a very nice and simple website designs that states clearly what we do as a company and that is easy for our customers to follow. We would like to have some moving pictures that are base on our expertise. We want the website to be easy to use and have the scroll down features that keeps things all on the same page when clicking on the menu. I attached a document with what we need on the website. I will also attach our logo. We want it to look simple clean and very professional.

Target Market(s)

Government Contracting, Management Consulting, Health

Industry/Entity Type

Government

Coding

Coded - Design and coding required

Number of Pages Required

1 page

Font styles to use
Serif

Requirements
Must have
• Very nice picture slides that speaks to our capabilities in Disaster Response, Strategic Planning, and Database Management. Slick look and design. Make sure SDVOSB Logo is right at the beginning of website as our customers is looking for that certification. Very nice colors that blend well with our logo.
Nice to have
• Very nice and slick colors that blends well with logo.
Should not have
• Basic website design that are weary on the eye. No bright colors, just simple colors that looks good with logo.

```html
<!DOCTYPE html>
<html lang="en">
<head>
<meta charset="utf-8">
<title>Pellworth &amp; Quine, LLC</title>
<link href="https://fonts.googleapis.com/css2?family=Merriweather:wght@400;700&family=Open+Sans:wght@400;600&display=swap" rel="stylesheet">
<style>
:root{
  --teal-900:#17303b;
  --teal-800:#1f3d4b;
  --teal-700:#2a4d5e;
  --teal-600:#2f5f73;
  --accent:#2c6b8f;
  --bright:#1e9be0;
  --ink:#2b2b2b;
  --muted:#5d6368;
  --paper:#ffffff;
  --mist:#eef0f1;
}
*{box-sizing:border-box;margin:0;padding:0}
html,body{width:1200px;height:3928px;overflow:hidden}
body{font-family:"Open Sans",Arial,sans-serif;color:var(--ink);background:var(--paper);position:relative}
h1,h2,h3,.serif{font-family:"Merriweather",Georgia,serif}
.btn{display:inline-block;background:var(--accent);color:#fff;font-size:13px;padding:10px 22px;border-radius:3px;letter-spacing:.5px}

/* header */
.site-header{position:absolute;top:0;left:0;width:1200px;height:140px;background:#fff;z-index:3}
.brand-panel{position:absolute;left:0;top:0;width:420px;height:140px}
.brand-name{position:absolute;left:52px;top:44px;color:#fff;font-family:"Merriweather",Georgia,serif;font-size:26px;font-weight:700;display:flex;align-items:center;gap:14px}
.brand-name .mark{width:18px;height:18px;background:#fff;border-radius:50%}
.main-nav{position:absolute;left:640px;top:44px;display:flex;gap:42px;font-size:15px;color:var(--teal-800)}
.main-nav a.active{border-bottom:2px solid var(--teal-800);padding-bottom:8px}
.cert-badge{position:absolute;left:1010px;top:16px;width:96px;height:96px;border-radius:50%;background:#c9d3da;border:4px solid #a83a3a}

/* hero */
.hero{position:absolute;top:0;left:0;width:1200px;height:760px}
.hero-photo{position:absolute;inset:0;background:radial-gradient(ellipse at 55% 45%,#a8742f 0%,#6b4a2a 35%,#3a3330 70%,#2c3438 100%)}
.hero-title{position:absolute;top:340px;width:100%;text-align:center;color:#fff;font-size:44px;font-weight:700;text-shadow:0 2px 6px rgba(0,0,0,.5)}
.hero-sub{position:absolute;top:408px;width:100%;text-align:center;color:#fff;font-size:18px;font-family:"Merriweather",Georgia,serif}
.hero-dots{position:absolute;left:1066px;top:330px;display:flex;flex-direction:column;gap:8px}
.hero-dots i{width:8px;height:8px;border-radius:50%;background:rgba(255,255,255,.6)}
.hero-dots i:first-child{background:#fff}
.social{position:absolute;left:1122px;top:218px;display:flex;flex-direction:column;gap:18px}
.social span{width:44px;height:44px;border-radius:50%;background:#fff;box-shadow:0 2px 6px rgba(0,0,0,.25)}
.hero-curve{position:absolute;bottom:0;left:0}

/* section heads */
.section-title{position:absolute;width:100%;text-align:center;font-size:38px;font-weight:400;color:var(--ink)}

.about-text{position:absolute;top:842px;left:150px;width:900px;text-align:center;font-size:14px;line-height:1.7;color:var(--muted)}
.about .btn{position:absolute;top:950px;left:542px}

/* leadership */
.leader{position:absolute;top:1146px;width:490px;height:340px;display:flex;gap:20px}
.leader-photo{width:210px;height:340px;background:linear-gradient(160deg,#d8d8d8,#9a9a9a)}
.leader-photo.alt{background:linear-gradient(160deg,#e9eef2,#b7c3cc)}
.leader-info h3{font-size:17px;color:var(--teal-800);margin-top:6px}
.leader-info .role{font-family:"Merriweather",Georgia,serif;font-style:italic;font-size:13px;color:var(--muted);margin:6px 0 14px}
.leader-info p{font-size:12px;line-height:1.65;color:var(--muted)}
.leader-info .btn{margin-top:14px;font-size:11px;padding:7px 14px}

/* capabilities */
.capabilities{position:absolute;top:1540px;left:0;width:1200px;height:500px}
.cap-wave{position:absolute;top:120px;left:0}
.cap-item{position:absolute;top:150px;width:300px;text-align:center}
.cap-item .diamond{margin:0 auto}
.cap-item p{margin-top:40px;font-family:"Merriweather",Georgia,serif;font-size:19px;line-height:1.4;color:var(--ink)}

/* why hire */
.why{position:absolute;top:2088px;left:0;width:1200px;height:530px;background:linear-gradient(90deg,#d9dee2,#f4f5f6)}
.why-photo{position:absolute;left:0;top:0;width:570px;height:530px;background:linear-gradient(135deg,#b7bec6 0%,#6d7882 45%,#3e4a55 100%)}
.why-content{position:absolute;left:690px;top:84px;width:430px}
.why-content h2{font-size:34px;font-weight:400;color:var(--teal-800);margin-bottom:26px}
.why-content ul{list-style:none}
.why-content li{position:relative;padding-left:22px;font-size:13px;line-height:1.6;color:var(--muted);margin-bottom:16px}
.why-content li::before{content:"";position:absolute;left:0;top:7px;width:8px;height:8px;border-radius:50%;background:var(--teal-800)}

/* agencies */
.agencies{position:absolute;top:2618px;left:0;width:1200px;height:144px;background:#fff;display:flex;align-items:center;padding-left:50px;gap:40px}
.agencies h2{font-size:32px;font-weight:400;margin-right:30px}
.agency-badge{width:96px;height:96px;border-radius:50%;background:#5d6a76}
.agency-badge.a{background:#3b5b3e}
.agency-badge.b{background:#2f4e8a}
.agency-badge.c{width:130px;height:70px;border-radius:4px;background:#2c4c8c}
.agency-badge.d{width:130px;height:84px;border-radius:4px;background:#1f5aa3}
.agency-badge.e{background:#263e6e}

/* partners */
.partners{position:absolute;top:2762px;left:0;width:1200px;height:440px;background:linear-gradient(180deg,#1e3b45 0%,#2c5060 50%,#1f3d4b 100%)}
.partners h2{position:absolute;top:28px;width:100%;text-align:center;color:#fff;font-size:28px;font-weight:400}
.partner-box{position:absolute;width:368px;height:140px;background:#fff;display:flex;align-items:center;justify-content:center;font-family:"Open Sans",Arial,sans-serif;font-weight:600;font-size:26px;color:#1b2a3a}

/* join */
.join{position:absolute;top:3218px;left:40px;width:1120px;height:104px;background:var(--teal-600);display:flex;align-items:center;padding:0 40px;color:#fff}
.join h3{font-size:22px;font-weight:400}
.join p{font-size:12px;opacity:.85;margin-top:6px}
.join form{margin-left:auto;display:flex}
.join .field{width:240px;height:46px;background:#fff;color:#888;font-size:13px;padding:14px}
.join .submit{height:46px;background:var(--bright);color:#fff;font-size:13px;padding:14px 24px}

/* footer */
.site-footer{position:absolute;top:3322px;left:0;width:1200px;height:566px;background:var(--teal-800);color:#fff}
.foot-brand{position:absolute;top:60px;width:100%;text-align:center;font-family:"Merriweather",Georgia,serif;font-size:26px;font-weight:700;display:flex;justify-content:center;align-items:center;gap:14px}
.foot-brand .mark{width:18px;height:18px;border-radius:50%;background:#fff}
.foot-text{position:absolute;top:116px;width:100%;text-align:center;font-size:13px;line-height:1.6;opacity:.85}
.contact-title{position:absolute;top:206px;width:100%;text-align:center;font-size:30px;font-weight:400}
.contact-list{position:absolute;left:190px;top:268px;list-style:none}
.contact-list li{display:flex;align-items:center;gap:20px;height:60px;margin-bottom:34px;font-size:13px;line-height:1.5}
.contact-list .ico{width:48px;height:48px;border-radius:50%;background:#fff;display:flex;align-items:center;justify-content:center;flex:none}
.contact-form{position:absolute;left:490px;top:262px;width:540px}
.contact-form .row{display:flex;gap:20px}
.contact-form .in{flex:1;height:40px;border-bottom:1px solid rgba(255,255,255,.4);font-size:12px;padding:12px 0;opacity:.9}
.contact-form .msg{height:92px}
.contact-form .btn{margin-top:18px;background:var(--teal-600)}
.copyright{position:absolute;top:3888px;left:0;width:1200px;height:40px;background:var(--teal-900);color:#cfd8dc;font-size:12px;text-align:center;line-height:40px}
</style>
</head>
<body>

<section class="hero">
  <div class="hero-photo" role="img" aria-label="Slide photo of firefighters in protective gear responding to an emergency"></div>
  <h1 class="hero-title">Pellworth &amp; Quine</h1>
  <p class="hero-sub">Disaster Response &nbsp;•&nbsp; Strategic Planning &nbsp;•&nbsp; Database Management</p>
  <div class="hero-dots"><i></i><i></i><i></i></div>
  <div class="social"><span></span><span></span><span></span><span></span></div>
  <svg class="hero-curve" width="1200" height="200" viewBox="0 0 1200 200"><path d="M0 110 Q600 260 1200 40 L1200 200 L0 200 Z" fill="#fff"/></svg>
</section>

<header class="site-header">
  <svg class="brand-panel" width="420" height="140" viewBox="0 0 420 140"><path d="M0 0 H420 L350 140 H0 Z" fill="#2a4d5e"/></svg>
  <div class="brand-name"><span class="mark"></span>Pellworth &amp; Quine</div>
  <nav class="main-nav"><a class="active">Home</a><a>About</a><a>Services</a><a>Contact</a></nav>
  <div class="cert-badge" role="img" aria-label="SDVOSB certification badge"></div>
</header>

<section class="about">
  <h2 class="section-title" style="top:776px">About Pellworth &amp; Quine</h2>
  <p class="about-text">Pellworth &amp; Quine, LLC is a minority owned Service Disabled Veteran Owned Small Business (SDVOSB) that provides Strategic Planning, Public Health Emergency Response, and Data Management Solutions for Federal Civilian and Defense Agencies. We have over 20 years of experience helping health and defense agencies develop concept of operations, deploy assets and personnel in Hot Zones around the world, and deliver goods and services all of the globe.</p>
  <span class="btn">Read More »</span>
</section>

<section class="leadership">
  <h2 class="section-title" style="top:1056px">Leadership Team</h2>
  <article class="leader" style="left:120px">
    <div class="leader-photo" role="img" aria-label="Portrait of the Chief Executive Officer"></div>
    <div class="leader-info">
      <h3>Ret. SFC Dana M. Pellworth</h3>
      <p class="role">Chief Executive Officer</p>
      <p>Dana founded the company after a long career of service in the Army, leading logistics teams across several continents. She has planned and led large field operations, supported emergency missions abroad, and now guides the firm in serving federal health and defense customers with care.</p>
      <span class="btn">READ MORE</span>
    </div>
  </article>
  <article class="leader" style="left:610px">
    <div class="leader-photo alt" role="img" aria-label="Portrait of the Business Development Manager"></div>
    <div class="leader-info">
      <h3>Mr. Gavin T. Marlow</h3>
      <p class="role">Business Development Manager</p>
      <p>Gavin brings over fifteen years of business development experience to the team. He has built partnerships with federal agencies and prime contractors, and he helps clients shape programs in planning, emergency response and data management across civilian and defense agencies nationwide.</p>
      <span class="btn">READ MORE</span>
    </div>
  </article>
</section>

<section class="capabilities">
  <h2 class="section-title" style="top:36px">Core Capabilities</h2>
  <svg class="cap-wave" width="1200" height="260" viewBox="0 0 1200 260"><path d="M0 180 C200 80 380 220 600 120 S980 60 1200 150 L1200 260 L0 260 Z" fill="#eef0f1"/><path d="M0 200 C240 110 420 240 640 150 S1000 90 1200 180" stroke="#d9dde0" fill="none" stroke-width="2"/></svg>
  <div class="cap-item" style="left:100px">
    <svg class="diamond" width="150" height="150" viewBox="0 0 150 150"><rect x="30" y="30" width="90" height="90" rx="8" transform="rotate(45 75 75)" fill="#2a4d5e"/><g fill="none" stroke="#fff" stroke-width="3"><circle cx="75" cy="62" r="9"/><circle cx="55" cy="72" r="6"/><circle cx="95" cy="72" r="6"/><path d="M60 95c0-12 30-12 30 0M44 95c0-8 10-10 14-8M106 95c0-8-10-10-14-8"/></g></svg>
    <p>Strategic Planning</p>
  </div>
  <div class="cap-item" style="left:450px">
    <svg class="diamond" width="150" height="150" viewBox="0 0 150 150"><rect x="30" y="30" width="90" height="90" rx="8" transform="rotate(45 75 75)" fill="#2a4d5e"/><g fill="none" stroke="#fff" stroke-width="3"><rect x="50" y="60" width="50" height="36" rx="3"/><path d="M65 60v-6h20v6M75 70v16M67 78h16"/></g></svg>
    <p>Public Health Emergency<br>Response</p>
  </div>
  <div class="cap-item" style="left:800px">
    <svg class="diamond" width="150" height="150" viewBox="0 0 150 150"><rect x="30" y="30" width="90" height="90" rx="8" transform="rotate(45 75 75)" fill="#2a4d5e"/><g fill="none" stroke="#fff" stroke-width="3"><rect x="48" y="56" width="54" height="36" rx="3"/><path d="M68 100h14M75 92v8M58 82l10-10 8 6 14-12"/></g></svg>
    <p>Data Management Services</p>
  </div>
</section>

<section class="why">
  <div class="why-photo" role="img" aria-label="Photo of a service member in uniform at a desk in front of a flag"></div>
  <div class="why-content">
    <h2>Why Hire Us?</h2>
    <ul>
      <li>Over 20 years of experience deploying assets and personnel in disaster zones around the US and the world.</li>
      <li>Over 20 years of experience developing concept of operations and stakeholder management strategies for Federal Agencies.</li>
      <li>Over 15 years of experience with database management and replications.</li>
      <li>Highly educated consultants with over 90% possessing advance degrees and industry certifications.</li>
    </ul>
    <span class="btn" style="margin-top:10px;font-size:11px;padding:7px 14px">READ MORE</span>
  </div>
</section>

<section class="agencies">
  <h2>Agencies We Serve</h2>
  <span class="agency-badge a"></span>
  <span class="agency-badge b"></span>
  <span class="agency-badge c"></span>
  <span class="agency-badge d"></span>
  <span class="agency-badge e"></span>
</section>

<section class="partners" role="img" aria-label="Background photo of soldiers in the field" >
  <h2>Our Partners</h2>
  <div class="partner-box" style="left:216px;top:100px">Caldera Advisory</div>
  <div class="partner-box" style="left:616px;top:100px;font-size:22px">Ostrander | Vail | Kemp</div>
  <div class="partner-box" style="left:216px;top:268px">Tessaline Aero</div>
  <div class="partner-box" style="left:616px;top:268px">Meridian Dynamics</div>
</section>

<section class="join">
  <div><h3 class="serif">Join Us</h3><p>Lorem ipsum a simple dummy text of the printing.</p></div>
  <form><div class="field">Enter Email Id</div><div class="submit">Submit Now</div></form>
</section>

<footer class="site-footer">
  <div class="foot-brand"><span class="mark"></span>Pellworth &amp; Quine</div>
  <p class="foot-text">Lorem amet with dolor sit aliquet mi. Ut suspendisse in tincidunt<br>nisl ante sodales. Fusce morbi sit.</p>
  <h2 class="contact-title">Contact Us</h2>
  <ul class="contact-list">
    <li><span class="ico"><svg width="20" height="24" viewBox="0 0 20 24"><path d="M10 1a8 8 0 0 0-8 8c0 6 8 14 8 14s8-8 8-14a8 8 0 0 0-8-8z" fill="#1f3d4b"/><circle cx="10" cy="9" r="3" fill="#fff"/></svg></span>1420 Larchmont Ave<br>Riverton, GA</li>
    <li><span class="ico"><svg width="22" height="22" viewBox="0 0 22 22"><path d="M5 2l4 4-2 3c1 3 3 5 6 6l3-2 4 4-3 3C9 20 2 13 2 5z" fill="#1f3d4b"/></svg></span>(555) 014-2287</li>
    <li><span class="ico"><svg width="24" height="18" viewBox="0 0 24 18"><rect x="1" y="1" width="22" height="16" rx="2" fill="#1f3d4b"/><path d="M2 3l10 7 10-7" stroke="#fff" stroke-width="2" fill="none"/></svg></span>info@pellworthquine.com</li>
  </ul>
  <div class="contact-form">
    <div class="row"><div class="in">Name</div><div class="in">Email</div></div>
    <div class="row"><div class="in">Subject</div></div>
    <div class="row"><div class="in msg">Message</div></div>
    <span class="btn">Submit</span>
  </div>
</footer>
<div class="copyright">© 2024 Copyright : pellworthquine.com . All Rights Reserved</div>

</body>
</html>
```